Website for Excavator and Earthworks Company

We require a modern, sleek and practical website for our newly created earthworks/excavator business in Perth, Western Australia called Bluegum Ridge Earthworks.

The website should have a modern, cutting edge feel but only needs to be relatively simplistic in it's layout and eventual functionality.

Some pages it should have would be Home, About, Projects and Contact Us.

```html
<!DOCTYPE html>
<html lang="en">
<head>
<meta charset="utf-8">
<title>Bluegum Ridge Earthworks</title>
<link href="https://fonts.googleapis.com/css2?family=Orbitron:wght@600;700&family=Lato:wght@400;700&display=swap" rel="stylesheet">
<style>
:root{
  --lime:#c9df12;
  --lime-deep:#b5cc06;
  --ink:#1c1d1f;
  --dark:#17181a;
  --text:#4a4a4a;
  --white:#ffffff;
  --line:#e2e2e2;
}
*{box-sizing:border-box;margin:0;padding:0}
html,body{width:1200px;height:3764px;overflow:hidden}
body{position:relative;background:var(--white);font-family:'Lato',sans-serif;color:var(--ink)}
.abs{position:absolute}
.heading{font-family:'Orbitron',sans-serif;font-weight:700;text-transform:uppercase;letter-spacing:1px;text-align:center}
.bar{position:absolute;height:6px;background:var(--lime);clip-path:polygon(4% 0,100% 0,96% 100%,0 100%)}
.btn{position:absolute;display:flex;align-items:center;justify-content:center;background:var(--lime);color:var(--ink);font-weight:700;font-size:17px;clip-path:polygon(8% 0,100% 0,92% 100%,0 100%)}

/* header */
.site-header{position:absolute;left:0;top:0;width:1200px;height:85px;background:var(--white)}
.brand{position:absolute;left:110px;top:20px;display:flex;align-items:center;gap:14px}
.brand-mark{width:44px;height:44px;background:var(--lime)}
.brand-name{font-family:'Orbitron',sans-serif;font-weight:700;font-size:21px;line-height:1.05;color:var(--ink)}
.nav a{position:absolute;top:32px;font-size:15px;color:var(--ink);text-decoration:none}
.nav .active{color:var(--lime-deep);text-decoration:underline}
.nav .cta{top:20px;left:932px;width:151px;height:46px;font-size:17px}

/* hero */
.hero-photo{position:absolute;left:0;top:85px;width:1200px;height:710px;background:linear-gradient(180deg,#6d7278 0%,#8c8f92 30%,#7a6a55 55%,#9a5c36 80%,#a0653d 100%)}
.hero-panel{position:absolute;left:120px;top:193px;width:954px;height:322px;background:rgba(30,30,30,.55)}
.hero-title{position:absolute;left:120px;top:205px;width:954px;font-size:54px;line-height:68px;color:var(--white)}
.hero-sub{position:absolute;left:220px;top:358px;width:754px;text-align:center;font-size:17px;font-weight:700;line-height:26px;color:var(--white)}
.hero-cut{position:absolute;left:0;top:660px}
.feature{position:absolute;width:200px;text-align:center;font-size:16px;color:var(--ink)}
.feature .dot{width:86px;height:86px;border-radius:50%;background:var(--lime);margin:0 auto 10px;display:flex;align-items:center;justify-content:center}

/* about */
.about-title{position:absolute;left:0;top:905px;width:1200px;font-size:38px}
.about-text{position:absolute;left:110px;top:1008px;width:980px;text-align:center;font-size:14.5px;line-height:26px;color:var(--text)}
.about-text p+p{margin-top:14px}

/* services */
.services-band{position:absolute;left:0;top:1305px;width:1200px;height:615px;background:linear-gradient(135deg,#cfe41a 0%,#c3d90e 50%,#d2e62a 100%);clip-path:polygon(0 0,100% 7%,100% 100%,0 93%)}
.services-title{position:absolute;left:0;top:1382px;width:1200px;font-size:38px;color:var(--ink)}
.service-card{position:absolute;top:1492px;width:306px;height:344px;border:2px solid var(--ink);background:var(--lime)}
.service-card .photo{height:294px;border-bottom:2px solid var(--ink)}
.service-card h3{font-size:20px;font-weight:700;text-align:center;line-height:46px}
.arrow{position:absolute;top:1648px;font-family:'Orbitron',sans-serif;font-weight:700;font-size:30px;color:var(--ink)}

/* why */
.why-title{position:absolute;left:0;top:1993px;width:1200px;font-size:38px}
.why-card{position:absolute;top:2096px;width:229px;height:258px;border:1px solid var(--line);box-shadow:0 2px 6px rgba(0,0,0,.12);text-align:center;background:var(--white)}
.why-card .ring{width:96px;height:96px;border-radius:50%;border:1.5px dashed var(--ink);margin:16px auto 0;display:flex;align-items:center;justify-content:center}
.why-card .ring span{width:84px;height:84px;border-radius:50%;background:var(--lime);display:flex;align-items:center;justify-content:center}
.why-card h4{font-size:18px;font-weight:400;margin-top:16px}
.why-card p{font-size:14px;line-height:26px;color:var(--text);margin-top:6px}
.why-card a{font-size:14px;font-style:italic;color:var(--text);line-height:30px}

/* call to action */
.cta-band{position:absolute;left:0;top:2438px;width:1200px;height:392px;background:linear-gradient(120deg,#1d1e20,#2a2a27 60%,#1a1b1c);clip-path:polygon(0 0,100% 8%,100% 100%,0 90%)}
.cta-title{position:absolute;left:0;top:2515px;width:1200px;font-size:40px;color:var(--lime)}
.cta-text{position:absolute;left:200px;top:2616px;width:800px;text-align:center;font-size:16px;line-height:26px;color:var(--white)}

/* video */
.video{position:absolute;left:110px;top:2913px;width:980px;height:397px;background:linear-gradient(180deg,#5a6b80 0%,#b8a27c 45%,#d4a65a 70%,#c59a63 100%);border:1px solid var(--line)}
.play{position:absolute;left:878px;top:40px;width:56px;height:56px;border-radius:50%;background:rgba(60,60,60,.85);display:flex;align-items:center;justify-content:center}

/* footer */
.footer-cut{position:absolute;left:0;top:3360px}
.footer{position:absolute;left:0;top:3380px;width:1200px;height:384px;background:var(--dark);clip-path:polygon(0 0,100% 24%,100% 100%,0 100%)}
.footer-brand{position:absolute;left:110px;top:3540px;width:250px;text-align:center;font-family:'Orbitron',sans-serif;font-weight:700;font-size:25px;line-height:30px;color:var(--white)}
.socials{position:absolute;left:110px;top:3654px;display:flex;gap:10px}
.socials span{width:22px;height:22px;border-radius:50%;background:var(--white)}
.col{position:absolute;top:3472px;color:var(--white)}
.col h5{font-size:16px;font-weight:400;margin-bottom:14px}
.col ul{list-style:none}
.col li{font-size:14px;line-height:34px;padding-left:22px;position:relative}
.col li::before{content:"";position:absolute;left:2px;top:14px;width:7px;height:7px;border-radius:50%;background:var(--white)}
.contact li{padding-left:26px;line-height:50px}
.contact li::before{display:none}
.contact svg{position:absolute;left:0;top:18px}
.footer-rule{position:absolute;left:110px;top:3705px;width:980px;height:1px;background:#444}
.legal{position:absolute;top:3718px;font-size:14px;color:var(--white)}
</style>
</head>
<body>

<header class="site-header">
  <div class="brand"><span class="brand-mark"></span><div class="brand-name">BLUEGUM RIDGE<br>EARTHWORKS</div></div>
  <nav class="nav">
    <a class="active" style="left:672px">Home</a>
    <a style="left:752px">About</a>
    <a style="left:829px">Projects</a>
    <a class="btn cta">Contact Us</a>
  </nav>
</header>

<section>
  <div class="hero-photo" role="img" aria-label="Yellow excavator on a red dirt site with mountains and cloudy sky"></div>
  <div class="hero-panel"></div>
  <h1 class="heading hero-title">Precision Earthworks<br>Built From The Ground Up</h1>
  <p class="hero-sub">Perth-based excavation and earthmoving services delivering reliable, efficient results for residential, commercial, and civil projects across Western Australia.</p>
  <a class="btn" style="left:503px;top:445px;width:194px;height:47px">Request a Quote</a>
  <svg class="hero-cut" width="1200" height="140" viewBox="0 0 1200 140">
    <polygon points="0,20 1200,125 1200,140 0,140" fill="#fff"/>
    <polygon points="0,18 1200,118 1200,131 0,31" fill="#c9df12"/>
  </svg>

  <div class="feature" style="left:72px;top:649px"><div class="dot"><svg width="40" height="40" viewBox="0 0 24 24"><path d="M12 2a7 7 0 0 0-7 7c0 5 7 13 7 13s7-8 7-13a7 7 0 0 0-7-7zm0 9.5A2.5 2.5 0 1 1 12 6.5a2.5 2.5 0 0 1 0 5z" fill="#1c1d1f"/></svg></div>Perth, WA Based</div>
  <div class="feature" style="left:283px;top:669px"><div class="dot"><svg width="44" height="44" viewBox="0 0 24 24"><circle cx="12" cy="12" r="7" fill="none" stroke="#1c1d1f" stroke-width="3" stroke-dasharray="3 2"/><circle cx="12" cy="12" r="3" fill="#1c1d1f"/></svg></div>Modern Equipment</div>
  <div class="feature" style="left:493px;top:682px"><div class="dot"><svg width="42" height="42" viewBox="0 0 24 24"><circle cx="12" cy="12" r="9" fill="none" stroke="#1c1d1f" stroke-width="2.5"/><path d="M12 7v5l3 3" stroke="#1c1d1f" stroke-width="2.5" fill="none" stroke-linecap="round"/></svg></div>Reliable &amp; On-Time</div>
  <div class="feature" style="left:704px;top:705px"><div class="dot"><svg width="40" height="40" viewBox="0 0 24 24"><path d="M12 2l8 3v6c0 5-3.5 9-8 11-4.5-2-8-6-8-11V5z" fill="#1c1d1f"/><path d="M8 12l3 3 5-6" stroke="#c9df12" stroke-width="2.2" fill="none"/></svg></div>Safety-First Approach</div>
</section>

<section>
  <h2 class="heading about-title">About Bluegum Ridge Earthworks</h2>
  <span class="bar" style="left:525px;top:969px;width:190px"></span>
  <div class="about-text">
    <p>Bluegum Ridge Earthworks is a Western Australian excavation and earthworks company built on precision, reliability, and modern methods. We specialise in practical, no-nonsense solutions that get projects moving — efficiently, safely, and to spec. Whether it's site preparation, trenching, or detailed earthmoving work, we approach every job with the same focus: doing it right the first time.</p>
    <p>From initial site preparation through to detailed excavation work, we take pride in clear communication, reliable scheduling, and workmanship that meets Australian standards. No shortcuts — just honest work done right.</p>
  </div>
  <a class="btn" style="left:523px;top:1175px;width:153px;height:47px">Read More</a>
</section>

<section>
  <div class="services-band"></div>
  <h2 class="heading services-title">Our Services</h2>
  <span class="bar" style="left:483px;top:1448px;width:234px;background:var(--ink)"></span>
  <span class="arrow" style="left:40px">«</span>
  <div class="service-card" style="left:110px"><div class="photo" role="img" aria-label="Excavator clearing scrub on a dusty site" style="background:linear-gradient(180deg,#8fa4bb,#7a7a5a 55%,#a07a4e)"></div><h3>Site Preparation &amp; Clearing</h3></div>
  <div class="service-card" style="left:446px"><div class="photo" role="img" aria-label="Dug trenches and concrete footings in soil" style="background:linear-gradient(180deg,#6e5a44,#8a7158 50%,#5a4534)"></div><h3>Trenching &amp; Footings</h3></div>
  <div class="service-card" style="left:784px"><div class="photo" role="img" aria-label="Excavator bucket resting on a prepared driveway pad" style="background:linear-gradient(180deg,#c9ced4,#3a3a3a 45%,#8f8f8a)"></div><h3>Driveways &amp; Pads</h3></div>
  <span class="arrow" style="left:1130px">»</span>
</section>

<section>
  <h2 class="heading why-title">Why Bluegum Ridge Earthworks?</h2>
  <span class="bar" style="left:483px;top:2057px;width:234px"></span>
  <div class="why-card" style="left:110px"><div class="ring"><span><svg width="44" height="44" viewBox="0 0 24 24"><circle cx="12" cy="12" r="8" fill="none" stroke="#1c1d1f" stroke-width="3" stroke-dasharray="3 2"/><circle cx="12" cy="12" r="3.5" fill="#1c1d1f"/></svg></span></div><h4>Modern Equipment</h4><p>We invest in up-to-date<br>machinery to deliver clean,</p><a>Read More</a></div>
  <div class="why-card" style="left:360px"><div class="ring"><span><svg width="44" height="44" viewBox="0 0 24 24"><circle cx="8" cy="8" r="3" fill="#1c1d1f"/><circle cx="16" cy="8" r="3" fill="#1c1d1f"/><path d="M3 20c0-4 2-7 5-7s5 3 5 7zM11 20c0-4 2-7 5-7s5 3 5 7z" fill="#1c1d1f"/></svg></span></div><h4>Straightforward</h4><p>We invest in up-to-date<br>machinery to deliver clean,</p><a>Read More</a></div>
  <div class="why-card" style="left:610px"><div class="ring"><span><svg width="42" height="42" viewBox="0 0 24 24"><path d="M12 2l8 3v6c0 5-3.5 9-8 11-4.5-2-8-6-8-11V5z" fill="#1c1d1f"/><path d="M8 12l3 3 5-6" stroke="#c9df12" stroke-width="2.2" fill="none"/></svg></span></div><h4>Safety &amp; Compliance</h4><p>We invest in up-to-date<br>machinery to deliver clean,</p><a>Read More</a></div>
  <div class="why-card" style="left:861px"><div class="ring"><span><svg width="46" height="46" viewBox="0 0 24 24"><rect x="2" y="7" width="12" height="9" fill="#1c1d1f"/><path d="M14 10h4l3 3v3h-7z" fill="#1c1d1f"/><circle cx="6" cy="18" r="2" fill="#1c1d1f"/><circle cx="17" cy="18" r="2" fill="#1c1d1f"/></svg></span></div><h4>Reliable Delivery</h4><p>We invest in up-to-date<br>machinery to deliver clean,</p><a>Read More</a></div>
</section>

<section>
  <div class="cta-band"></div>
  <h2 class="heading cta-title">Let's Get Your Project Moving</h2>
  <span class="bar" style="left:483px;top:2582px;width:234px"></span>
  <p class="cta-text">If you're planning an excavation or earthworks project in Perth or across Western Australia, Bluegum Ridge Earthworks is ready to help.</p>
  <a class="btn" style="left:505px;top:2695px;width:192px;height:47px">Request a Quote</a>
</section>

<section>
  <div class="video" role="img" aria-label="Excavator loading a tipper truck on a sunlit earthworks site">
    <span class="play"><svg width="22" height="22" viewBox="0 0 24 24"><path d="M7 4l13 8-13 8z" fill="#fff"/></svg></span>
  </div>
</section>

<footer>
  <svg class="footer-cut" width="1200" height="120" viewBox="0 0 1200 120">
    <polygon points="0,10 1200,100 1200,115 0,25" fill="#c9df12"/>
  </svg>
  <div class="footer"></div>
  <div class="footer-brand">BLUEGUM RIDGE<br>EARTHWORKS</div>
  <div class="socials"><span></span><span></span><span></span><span></span></div>

  <div class="col" style="left:430px"><h5>Quick Links</h5><ul><li>Home</li><li>About</li><li>Services</li><li>Projects</li><li>Contact</li></ul></div>
  <div class="col" style="left:594px"><h5>Services</h5><ul><li>Site Preparation</li><li>Excavation</li><li>Trenching &amp; Footings</li><li>Earthmoving</li><li>Drainage Works</li></ul></div>
  <div class="col contact" style="left:837px"><h5>Contact Us</h5><ul>
    <li><svg width="16" height="16" viewBox="0 0 24 24"><circle cx="12" cy="12" r="11" fill="#fff"/><path d="M8 6l2 3-1.5 1.5a8 8 0 0 0 5 5L15 14l3 2-1 3c-6 0-11-5-11-11z" fill="#17181a"/></svg>+61 8 9000 4127</li>
    <li><svg width="16" height="16" viewBox="0 0 24 24"><circle cx="12" cy="12" r="11" fill="#fff"/><rect x="6" y="8" width="12" height="8" fill="none" stroke="#17181a" stroke-width="1.6"/><path d="M6 8l6 5 6-5" fill="none" stroke="#17181a" stroke-width="1.6"/></svg>hello@bluegumridgeworks.com.au</li>
    <li><svg width="16" height="16" viewBox="0 0 24 24"><path d="M12 1a8 8 0 0 0-8 8c0 6 8 14 8 14s8-8 8-14a8 8 0 0 0-8-8zm0 11a3 3 0 1 1 0-6 3 3 0 0 1 0 6z" fill="#fff"/></svg>Perth, Western Australia</li>
  </ul></div>

  <div class="footer-rule"></div>
  <p class="legal" style="left:110px">Privacy Policy | Terms &amp; Conditions</p>
  <p class="legal" style="left:772px">© Bluegum Ridge Earthworks. All Rights Reserved.</p>
</footer>

</body>
</html>
```